Craft Beer Company

We need a web design for our Tampa based craft beer company that shows and tells what we are about and our products, up and coming beers, events and happenings. Must has a verify age by selecting yes or no to "are you 21 years or older.. have logos and product labels etc... currently have Plimtora.com a our website, thats under construction.
Reason: more time to be thorough
Target Market(s)
Craft Beer Enthusiasts , Craft Beer Community
Industry/Entity Type
Construction
Requirements
Must have
- The pages on the site should have, about us, events, our beer, store for e-commerce
being that we are set up with Plimtora.com I would like to contineu to use them, unless there is another option available. We have the domain there.

```html
<!DOCTYPE html>
<html lang="en">
<head>
<meta charset="utf-8">
<title>Harborline Beer Company</title>
<link href="https://fonts.googleapis.com/css2?family=Alegreya:ital,wght@0,400;1,400&family=Open+Sans:wght@400;600&display=swap" rel="stylesheet">
<style>
:root{
  --nav-bg:#232323;
  --green:#7cb53a;
  --green-light:#9ccc4c;
  --ink:#2b2b2b;
  --grey-text:#8f8f8f;
  --white:#ffffff;
  --footer-bg:#262626;
  --link-blue:#3f7fc0;
  --amber-1:#e2b44a;
  --amber-2:#8a5a14;
}
*{box-sizing:border-box;margin:0;padding:0}
html,body{width:1200px;height:2222px;overflow:hidden}
body{position:relative;background:var(--white);font-family:"Open Sans",Arial,sans-serif;color:var(--ink)}
.abs{position:absolute}

/* header */
.site-header{position:absolute;left:0;top:0;width:1200px;height:108px;background:var(--nav-bg)}
.brand{position:absolute;left:59px;top:36px;display:flex;align-items:center;gap:8px;color:var(--green-light);font-size:16px;font-weight:600}
.brand-dot{width:30px;height:30px;border-radius:50%;background:var(--green)}
.main-nav a{position:absolute;top:0;height:108px;line-height:104px;font-size:16px;color:var(--green-light);text-decoration:none}
.main-nav a.active{left:222px;width:102px;text-align:center;background:var(--green);color:var(--white)}

/* hero */
.hero{position:absolute;left:0;top:108px;width:1200px;height:689px;
  background:radial-gradient(ellipse at 50% 45%,#f2d779 0%,var(--amber-1) 35%,#b07b22 70%,#5a3a10 100%)}
.hero-badge{position:absolute;left:967px;top:27px;width:154px;height:154px;border-radius:50%;border:6px solid rgba(240,230,210,.8);
  display:flex;align-items:center;justify-content:center;text-align:center;font-family:"Alegreya",Georgia,serif;font-size:22px;line-height:27px;color:#3a2a14}
.hero-text{position:absolute;left:0;width:1200px;text-align:center;font-family:"Alegreya",Georgia,serif;color:var(--white)}
.hero-welcome{top:205px;font-size:60px}
.hero-title{top:265px;font-size:64px}
.hero-sub{top:333px;font-size:38px;font-style:italic}
.hero-arrow{position:absolute;top:320px}

/* section headings */
.section-title{position:absolute;font-size:29px;font-weight:400;color:var(--ink)}
.section-title span{color:var(--green)}
.section-title.light{color:var(--white)}

/* beer cards */
.beer-card{position:absolute;top:883px;width:340px;height:290px;text-align:center;color:var(--white);box-shadow:0 2px 8px rgba(0,0,0,.3)}
.beer-card h3{position:absolute;top:117px;width:100%;font-size:20px;font-weight:400}
.beer-card p{position:absolute;top:152px;width:100%;font-size:16px;color:var(--green-light)}
.beer-card svg{position:absolute;left:160px;top:180px}

/* events */
.events{position:absolute;left:0;top:1210px;width:1200px;height:501px;
  background:linear-gradient(180deg,#3a2a18 0%,#1c130b 60%,#120c07 100%)}
.event{position:absolute;top:88px;width:339px;color:var(--white)}
.event-photo{width:339px;height:191px}
.event h4{margin:24px 6px 0;font-size:17px;font-weight:400;letter-spacing:.3px}
.event time{display:block;margin:2px 6px 0;font-size:13px;color:var(--green-light)}
.event p{margin:16px 6px 0;font-size:12.5px;line-height:22px;text-align:justify;font-weight:600;color:#e8e2d8}
.event a{display:block;text-align:right;margin:18px 6px 0;font-size:15px;color:var(--green-light);text-decoration:underline}

/* feeds */
.feed-page{position:absolute;left:59px;top:1800px;width:60px;height:60px;background:var(--green)}
.like-row{position:absolute;left:134px;top:1837px;display:flex;align-items:center;gap:8px;font-size:10px;color:var(--ink)}
.like-btn{border:1px solid #c8c8c8;background:#f2f2f2;padding:1px 5px;font-size:10px;color:#3b5b98}
.like-sq{width:14px;height:14px;background:#3b5b98;border-radius:2px}
.feed-item{position:absolute;left:59px;width:500px}
.feed-photo{position:absolute;left:0;top:0;width:90px;height:72px}
.feed-body{position:absolute;left:126px;top:-2px;width:410px}
.feed-body h5{font-size:17px;font-weight:400;color:var(--link-blue)}
.feed-body p{margin-top:4px;font-size:13px;line-height:22px;color:var(--grey-text)}
.feed-meta{margin-top:6px;font-size:10px;color:var(--grey-text)}
.feed-meta span{margin-left:14px;color:var(--link-blue)}

/* about */
.about-text{position:absolute;left:600px;width:318px;font-size:13px;line-height:22px;color:var(--grey-text);text-align:justify}
.about-more{position:absolute;left:600px;top:1988px;display:flex;align-items:center;gap:12px;font-size:14px;color:var(--green)}
.poster{position:absolute;left:967px;top:1801px;width:172px;height:251px;border:1px solid #999}

/* footer */
.site-footer{position:absolute;left:0;top:2105px;width:1200px;height:117px;background:var(--footer-bg)}
.social{position:absolute;top:25px;width:36px;height:36px;border-radius:50%;background:#0d0d0d}
.copyright{position:absolute;top:76px;width:1200px;text-align:center;font-size:10px;color:#8a8a8a}
</style>
</head>
<body>

<header class="site-header">
  <div class="brand"><span class="brand-dot"></span>Harborline</div>
  <nav class="main-nav">
    <a class="active" href="#">Home</a>
    <a href="#" style="left:352px">About Us</a>
    <a href="#" style="left:478px">Upcoming Beers</a>
    <a href="#" style="left:665px">Events &amp; Happenings</a>
    <a href="#" style="left:884px">Our History</a>
    <a href="#" style="left:1025px">Contact Us</a>
  </nav>
</header>

<section class="hero" role="img" aria-label="Photo of a row of beer glasses filled with golden and amber beer">
  <div class="hero-badge">Harborline<br>Beer<br>Company</div>
  <div class="hero-text hero-welcome">Welcome</div>
  <div class="hero-text hero-title">Lorem ipsum dolor sit amet</div>
  <div class="hero-text hero-sub">Consectetuer Adipiscingtelit Pellentesque Sed dvolor.</div>
  <svg class="hero-arrow" style="left:60px" width="16" height="26" viewBox="0 0 16 26"><path d="M13 2 3 13l10 11" fill="none" stroke="#fff" stroke-width="3"/></svg>
  <svg class="hero-arrow" style="left:1124px" width="16" height="26" viewBox="0 0 16 26"><path d="M3 2l10 11L3 24" fill="none" stroke="#fff" stroke-width="3"/></svg>
</section>

<h2 class="section-title" style="left:59px;top:822px">Upcoming <span>Beers</span></h2>

<article class="beer-card" style="left:59px;background:linear-gradient(180deg,#8a8a8a,#7a7670)" role="img" aria-label="Photo of a pint glass of beer">
  <h3>Fusce suscipit varius</h3><p>Diam nonummy</p>
  <svg width="20" height="20" viewBox="0 0 20 20"><g fill="none" stroke="#fff" stroke-width="3"><rect x="2" y="2" width="9" height="6" rx="3" transform="rotate(45 6.5 5)"/><rect x="9" y="12" width="9" height="6" rx="3" transform="rotate(45 13.5 15)"/></g></svg>
</article>
<article class="beer-card" style="left:430px;background:linear-gradient(180deg,#a8803c,#6e4a1c)" role="img" aria-label="Photo of glasses of lager on a table">
  <h3>Sed ut perspiciatis unde</h3><p>Veritatis et quasi</p>
  <svg width="20" height="20" viewBox="0 0 20 20"><g fill="none" stroke="#fff" stroke-width="3"><rect x="2" y="2" width="9" height="6" rx="3" transform="rotate(45 6.5 5)"/><rect x="9" y="12" width="9" height="6" rx="3" transform="rotate(45 13.5 15)"/></g></svg>
</article>
<article class="beer-card" style="left:801px;background:linear-gradient(180deg,#4a3620,#2a1e12)" role="img" aria-label="Photo of a beer glass beside a jug with hops">
  <h3>Nem ipsam voluptatem</h3><p>Dicta sunt explicabo</p>
  <svg width="20" height="20" viewBox="0 0 20 20"><g fill="none" stroke="#fff" stroke-width="3"><rect x="2" y="2" width="9" height="6" rx="3" transform="rotate(45 6.5 5)"/><rect x="9" y="12" width="9" height="6" rx="3" transform="rotate(45 13.5 15)"/></g></svg>
</article>

<section class="events" role="img" aria-label="Background photo of a crowd at a concert in warm light">
  <h2 class="section-title light" style="left:59px;top:28px">Events &amp; <span>Happenings</span></h2>
  <article class="event" style="left:59px">
    <div class="event-photo" role="img" aria-label="Photo of friends toasting with beer mugs" style="background:linear-gradient(135deg,#6a4a2c,#b58a4a)"></div>
    <h4>NULLA VENENATIS IN PEDE MI</h4><time>November 23, 2014</time>
    <p>Vestibulum molestie. Aenean nonummy hendrerimauris. Phasellus porta. Fusce suscipit varius mi. Cum socis natoque penatibus et magnis dis parturient montes.</p>
    <a href="#">Read More</a>
  </article>
  <article class="event" style="left:430px">
    <div class="event-photo" role="img" aria-label="Photo of a concert stage with bright lights and raised hands" style="background:radial-gradient(circle at 50% 30%,#ffd070,#d0601a 40%,#2a2a6a 80%)"></div>
    <h4>NULLA VENENATIS IN PEDE MI</h4><time>November 23, 2014</time>
    <p>Vestibulum molestie. Aenean nonummy hendrerimauris. Phasellus porta. Fusce suscipit varius mi. Cum socis natoque penatibus et magnis dis parturient montes.</p>
    <a href="#">Read More</a>
  </article>
  <article class="event" style="left:801px">
    <div class="event-photo" role="img" aria-label="Photo of a group of guests holding brewery signs at a bar" style="background:linear-gradient(135deg,#3a2a22,#6a5040)"></div>
    <h4>NULLA VENENATIS IN PEDE MI</h4><time>November 23, 2014</time>
    <p>Vestibulum molestie. Aenean nonummy hendrerimauris. Phasellus porta. Fusce suscipit varius mi. Cum socis natoque penatibus et magnis dis parturient montes.</p>
    <a href="#">Read More</a>
  </article>
</section>

<h2 class="section-title" style="left:59px;top:1737px">Social <span>Feeds</span></h2>
<div class="feed-page" role="img" aria-label="Brewery page image"></div>
<div class="like-row"><span class="like-btn">Like</span><span class="like-sq"></span><span>111,865,65 people like this. Be the first of your friends</span></div>

<div class="feed-item" style="top:1884px">
  <div class="feed-photo" role="img" aria-label="Profile photo of a couple" style="background:linear-gradient(135deg,#d8b8a0,#8a6a58)"></div>
  <div class="feed-body"><h5>Lorem ipsum dolor sit amet</h5>
    <p>consectetuer adipiscing elit. Pellentesque sed dolor. Aliquam congue ermentum nisl. Mauris accumsan nulla vel diam.</p>
    <div class="feed-meta">24 minutes ago<span>Likes</span><span>Comments</span><span>Share</span></div></div>
</div>
<div class="feed-item" style="top:1994px">
  <div class="feed-photo" role="img" aria-label="Profile photo of a woman in a sun hat" style="background:linear-gradient(135deg,#e8dcc8,#a8886a)"></div>
  <div class="feed-body"><h5>Lorem ipsum dolor sit amet</h5>
    <p>consectetuer adipiscing elit. Pellentesque sed dolor. Aliquam congue ermentum nisl. Mauris accumsan nulla vel diam.</p>
    <div class="feed-meta">24 minutes ago<span>Likes</span><span>Comments</span><span>Share</span></div></div>
</div>

<h2 class="section-title" style="left:600px;top:1737px">About <span>Us</span></h2>
<p class="about-text" style="top:1795px">Fusce euismod consequat ante. Lorem ipsum dolor sit amet, consectetuer adipiscing elit. Pellentesque sed dolor. Aliquam congue fermentum nisl.Fusce euismod consequat ante.</p>
<p class="about-text" style="top:1906px">Lorem ipsum dolor sit amet, consectetuer adipiscing elit. Pellentesque sed dolor. Aliquam congue fermentum nisl. Mauris accumsan nulla vel diam.</p>
<div class="about-more">What Else Is There
  <svg width="18" height="18" viewBox="0 0 18 18"><circle cx="9" cy="9" r="9" fill="var(--green)"/><path d="M5 9h7M9 5.5 12.5 9 9 12.5" fill="none" stroke="#fff" stroke-width="2"/></svg></div>
<div class="poster" role="img" aria-label="Event poster for an IPA release with palm tree artwork" style="background:linear-gradient(180deg,#2a1a10,#7a3a14 45%,#d88a2a 60%,#2a1a10)"></div>

<footer class="site-footer">
  <span class="social" style="left:533px"></span>
  <span class="social" style="left:582px"></span>
  <span class="social" style="left:631px"></span>
  <p class="copyright">© 2014 Harborline Beer Company.All Rights Reserved &nbsp;|&nbsp; Privacy Policy</p>
</footer>

</body>
</html>
```